Redesign of business card for Cedar Ridge Mechanical

We are looking for a new design for our business cards for Cedar Ridge Mechanical. We are a plumbing & HVAC construction company, operating on the West Coast of Canada and USA. Logo attached.
Industry/Entity Type
Construction - Plumbing & HVAC
Contact Information for Business Card
Name, address, phone numbers, email, website address
Look and feel
Each slider illustrates characteristics of the customer's brand and the style your logo design should communicate.

```html
<!DOCTYPE html>
<html lang="en">
<head>
<meta charset="utf-8">
<title>Cedar Ridge Mechanical – Business Card</title>
<link rel="stylesheet" href="https://fonts.googleapis.com/css2?family=Montserrat:wght@400;500;600;700&display=swap">
<style>
  :root {
    --page-bg: #e9e6e1;
    --card-light: #e6dfd3;
    --panel-dark: #141414;
    --panel-mid: #2a2a2a;
    --swoosh-grey: #8a857d;
    --swoosh-light: #c9c2b6;
    --text-gold: #cbbfa9;
    --text-soft: #b8ae9c;
    --brand-ink: #1b1b1b;
  }
  * { margin: 0; padding: 0; box-sizing: border-box; }
  html, body {
    width: 1200px; height: 1047px; overflow: hidden;
    background: var(--page-bg);
    font-family: "Montserrat", sans-serif;
  }
  .business-card {
    position: absolute; left: 160px; top: 281px;
    width: 880px; height: 485px;
    border-radius: 22px; overflow: hidden;
    background: var(--card-light);
    box-shadow: 0 12px 36px rgba(0,0,0,0.18);
  }
  .card-shape { position: absolute; inset: 0; }
  .contact-panel {
    position: absolute; left: 36px; top: 152px;
    color: var(--text-soft);
  }
  .person-name {
    font-size: 31px; font-weight: 700; letter-spacing: 1px;
    color: var(--text-gold);
  }
  .person-role { font-size: 22px; font-weight: 500; margin-top: 6px; }
  .address { font-size: 22px; font-weight: 500; line-height: 34px; margin-top: 36px; }
  .contact-list { list-style: none; margin-top: 34px; }
  .contact-item {
    display: flex; align-items: center; gap: 12px;
    font-size: 22px; font-weight: 500; height: 34px;
  }
  .contact-icon { width: 20px; height: 20px; fill: var(--text-soft); }
  .brand-block {
    position: absolute; left: 500px; top: 168px; width: 350px;
    display: flex; align-items: center; gap: 18px;
    color: var(--brand-ink);
  }
  .brand-square {
    width: 58px; height: 58px; flex: none;
    background: var(--brand-ink);
  }
  .brand-name {
    font-size: 30px; font-weight: 700; line-height: 36px;
    text-transform: uppercase; letter-spacing: 1px;
  }
</style>
</head>
<body>
  <div class="business-card">
    <svg class="card-shape" viewBox="0 0 880 485" width="880" height="485" aria-hidden="true">
      <defs>
        <linearGradient id="panelShade" x1="0" y1="0" x2="1" y2="1">
          <stop offset="0" stop-color="#262626"/>
          <stop offset="0.6" stop-color="#161616"/>
          <stop offset="1" stop-color="#0e0e0e"/>
        </linearGradient>
      </defs>
      <path d="M505,0 C480,60 430,110 410,190 C388,280 395,360 470,485 L520,485 C440,380 420,290 445,200 C462,130 490,70 515,0 Z" fill="var(--swoosh-light)"/>
      <path d="M470,70 C440,120 420,200 418,270 C418,360 455,430 500,485 L482,485 C430,420 400,350 402,270 C404,190 430,120 470,70 Z" fill="var(--swoosh-grey)"/>
      <path d="M0,0 H495 C470,50 420,110 400,190 C380,270 385,350 450,485 H0 Z" fill="url(#panelShade)"/>
      <path d="M475,130 C445,190 430,260 440,330 C450,390 475,430 505,470 C460,420 430,370 422,320 C412,250 435,180 475,130 Z" fill="#1d1d1d"/>
    </svg>

    <div class="contact-panel">
      <h1 class="person-name">MARK ELLISON</h1>
      <p class="person-role">Managing Director</p>
      <p class="address">Your address, City<br>State, Zip 1234</p>
      <ul class="contact-list">
        <li class="contact-item">
          <svg class="contact-icon" viewBox="0 0 24 24"><path d="M3 9c0-3 4-5 9-5s9 2 9 5l-3 2-3-2V7H9v2l-3 2-3-2zm3 3h12l2 8H4z"/></svg>
          123 456 789
        </li>
        <li class="contact-item">
          <svg class="contact-icon" viewBox="0 0 24 24"><path d="M2 6h20v13H2zm2 2v1l8 5 8-5V8l-8 5z"/></svg>
          info@youremail.com
        </li>
        <li class="contact-item">
          <svg class="contact-icon" viewBox="0 0 24 24"><circle cx="12" cy="12" r="9"/></svg>
          www.yourwebsite.com
        </li>
      </ul>
    </div>

    <div class="brand-block">
      <span class="brand-square"></span>
      <span class="brand-name">Cedar Ridge<br>Mechanical</span>
    </div>
  </div>
</body>
</html>
```